Website Design for Employee Moral and Happiness Company

Looking for a clean website design that explains our features in a step by step manner so our visitors know exactly what our site does before logging in.

The site is called "Velrato". See logo design and video for a sample of style and an overview of what we do.

Target Market(s)

Business owners that are looking to retain employees.

Number of Pages Required

1 page

```html
<!DOCTYPE html>
<html lang="en">
<head>
<meta charset="utf-8">
<title>Velrato – Employee Happiness</title>
<link href="https://fonts.googleapis.com/css2?family=Poppins:wght@400;500;600;700;800&display=swap" rel="stylesheet">
<style>
:root{
  --orange:#ff6a00;
  --orange-soft:#ff9a4d;
  --ink:#111111;
  --text:#333333;
  --muted:#555555;
  --light:#f3f3f3;
  --band:#dcdcdc;
  --white:#ffffff;
}
*{margin:0;padding:0;box-sizing:border-box}
html,body{width:1200px;height:4241px;overflow:hidden}
body{position:relative;font-family:'Poppins',sans-serif;color:var(--text);background:var(--white)}
.abs{position:absolute}
.topbar{left:678px;top:0;width:522px;height:40px;background:var(--orange);border-bottom-left-radius:28px;color:var(--white);font-size:15px;display:flex;align-items:center;gap:26px;padding-left:56px}
.topbar span{display:flex;align-items:center;gap:10px}
.brand{left:79px;top:28px;font-size:38px;font-weight:600;color:var(--ink);letter-spacing:1px;line-height:1.2}
.nav{top:66px;font-size:15px;font-weight:500;color:#444;line-height:20px}
.nav.active{color:var(--orange)}
.nav.active::after{content:"• • •";position:absolute;left:12px;top:18px;font-size:9px;letter-spacing:-1px}
.login{left:935px;top:56px;width:150px;height:41px;border:2px solid #555;border-radius:22px;color:var(--orange);font-weight:600;font-size:14px;display:flex;align-items:center;justify-content:center;gap:6px}
.hero-kicker{left:79px;top:214px;font-size:33px;font-weight:400;color:var(--ink);letter-spacing:1px;display:flex;align-items:center;gap:14px;line-height:46px}
.hero-kicker::after{content:"";width:102px;height:2px;background:var(--ink)}
.hero-title{left:78px;top:264px;font-size:72px;font-weight:800;color:var(--ink);letter-spacing:-1px;line-height:72px}
.hero-text{left:79px;top:338px;font-size:20px;line-height:34px;color:var(--ink)}
.btn{display:flex;align-items:center;justify-content:center;border-radius:28px;font-weight:700;font-size:15px;letter-spacing:.3px}
.btn-fill{background:var(--orange);color:var(--white)}
.btn-line{border:2px solid var(--orange);color:var(--ink);background:var(--white)}
.btn-dark{background:var(--ink);color:var(--white)}
.slide-arrow{top:270px;width:33px;height:71px;background:#8a8a8a;color:var(--white);display:flex;align-items:center;justify-content:center;font-size:20px}
.art{border-radius:20px}
.badge{left:568px;top:584px;width:240px;height:66px;background:var(--white);border-radius:33px;box-shadow:0 6px 20px rgba(0,0,0,.12);display:flex;align-items:center;gap:14px;padding-left:26px}
.badge i{width:32px;height:32px;border-radius:50%;background:var(--orange)}
.badge b{font-size:15px;font-weight:500;color:var(--ink);line-height:18px;border-left:1px solid #aaa;padding-left:12px}
.badge b em{display:block;font-style:normal;color:var(--orange);font-weight:700;font-size:18px}
.down{left:563px;top:696px;width:72px;height:72px;border-radius:50%;background:var(--band);display:flex;align-items:center;justify-content:center}
.h2{font-size:44px;font-weight:800;color:var(--ink);letter-spacing:-.5px;line-height:60px}
.body{font-size:18.5px;line-height:34px;color:var(--text)}
.feature-title{font-size:19px;font-weight:700;color:var(--white);line-height:28px}
.feature-text{font-size:18.5px;line-height:35px;color:var(--white)}
.ficon{width:88px;height:88px;border-radius:50%;background:var(--white);display:flex;align-items:center;justify-content:center}
.list li{list-style:none;display:flex;align-items:center;gap:10px;font-size:18.5px;height:43px}
.tick{width:18px;height:18px;border-radius:50%;background:var(--orange);display:flex;align-items:center;justify-content:center}
.contact{left:0;top:3280px;width:1200px;height:580px;background:#000}
.field{background:var(--white);border-radius:3px;font-size:15px;color:#444;padding:16px 18px}
.fh{top:3926px;font-size:20px;font-weight:800;color:var(--ink)}
.flist{font-size:16.5px;line-height:33.8px;color:#444}
.social{width:44px;height:44px;border:2px solid var(--orange);border-radius:8px;top:4083px}
.cicon{width:48px;height:48px;background:var(--orange);border-radius:8px;display:flex;align-items:center;justify-content:center}
</style>
</head>
<body>

<!-- header -->
<div class="abs topbar">
  <span><svg width="16" height="16" viewBox="0 0 24 24"><path fill="#fff" d="M6.6 10.8a15 15 0 0 0 6.6 6.6l2.2-2.2c.3-.3.7-.4 1-.2 1.1.4 2.3.6 3.6.6.6 0 1 .4 1 1V20c0 .6-.4 1-1 1A17 17 0 0 1 3 4c0-.6.4-1 1-1h3.5c.6 0 1 .4 1 1 0 1.3.2 2.5.6 3.6.1.3 0 .7-.2 1z"/></svg>555-318-2046</span>
  <span style="opacity:.8">|</span>
  <span><svg width="18" height="16" viewBox="0 0 24 20"><rect x="1" y="3" width="22" height="16" rx="2" fill="#fff"/><path d="M2 5l10 7 10-7" stroke="#ff6a00" stroke-width="2" fill="none"/></svg>info@velrato.com</span>
</div>
<div class="abs brand">Velrato</div>
<div class="abs nav active" style="left:428px">HOME</div>
<div class="abs nav" style="left:502px">ABOUT US</div>
<div class="abs nav" style="left:611px">OUR FEATURES</div>
<div class="abs nav" style="left:754px">BLOG</div>
<div class="abs nav" style="left:825px">CONTACT</div>
<div class="abs login"><svg width="14" height="16" viewBox="0 0 14 16"><circle cx="7" cy="4.5" r="3.5" fill="none" stroke="#ff6a00" stroke-width="1.6"/><path d="M1 15.5c0-3.5 2.7-5.5 6-5.5s6 2 6 5.5" fill="none" stroke="#ff6a00" stroke-width="1.6"/></svg>| LOG IN</div>

<!-- hero -->
<svg class="abs" style="left:0;top:114px" width="1200" height="660" viewBox="0 0 1200 660">
  <path d="M90 470 Q600 800 1110 470 Q600 740 90 470 Z" fill="var(--band)"/>
  <path d="M0 0 H1200 V420 Q600 840 0 420 Z" fill="var(--light)"/>
</svg>
<div class="abs hero-kicker">To Help Business</div>
<div class="abs hero-title">LIKE YOURS</div>
<div class="abs hero-text">Lorem ipsum dolor sit amet consectetuo<br>nun adipis elitsed do eiusmod tempor</div>
<div class="abs btn btn-fill" style="left:79px;top:426px;width:214px;height:53px">CONTACT US</div>
<div class="abs slide-arrow" style="left:0">‹</div>
<div class="abs slide-arrow" style="left:1167px">›</div>
<div class="abs art" role="img" aria-label="Illustration of a team meeting around an office desk" style="left:543px;top:148px;width:560px;height:420px;background:linear-gradient(135deg,#ececec,#f7c7a3)"></div>
<div class="abs badge"><i></i><b>EMPLOYEE<em>HAPPINESS</em></b></div>
<div class="abs down"><svg width="20" height="30" viewBox="0 0 20 30"><path d="M10 2v25M3 20l7 7 7-7" stroke="#333" stroke-width="2" fill="none"/></svg></div>

<!-- about -->
<div class="abs art" role="img" aria-label="Illustration of colleagues working together at a table with laptops" style="left:74px;top:815px;width:510px;height:485px;border-radius:50%;background:radial-gradient(circle,#fde3cf,#f6f6f6)"></div>
<div class="abs h2" style="left:635px;top:888px">ABOUT US</div>
<div class="abs body" style="left:635px;top:957px;width:500px">Lorem ipsum dolor sit amet consectetur adipiscingi elit sed do eiusmod tempor incididunt ut labore eto dolore magna aliqua. Quis ipsum suspendisse des ultrices gravida. Risus commodo viverra maecenas accumsan lacus vel facilisis licius decorat.</div>
<div class="abs btn btn-fill" style="left:635px;top:1157px;width:188px;height:53px">ABOUT US</div>

<!-- features -->
<svg class="abs" style="left:0;top:1374px" width="1200" height="832" viewBox="0 0 1200 832">
  <defs><linearGradient id="fg" x1="0" y1="0" x2="0" y2="1"><stop offset="0" stop-color="#ff6a00"/><stop offset="1" stop-color="#ff9a4d"/></linearGradient></defs>
  <path d="M0 156 Q600 -156 1200 156 L1200 680 Q600 984 0 680 Z" fill="url(#fg)"/>
</svg>
<div class="abs h2" style="left:0;width:1200px;text-align:center;top:1426px;color:var(--white)">OUR FEATURE</div>
<div class="abs feature-text" style="left:0;width:1200px;text-align:center;top:1494px;line-height:34px">Lorem ipsum dolor sit amet consectetur adipiscingi<br>elit sed do eiusmod tempor incididunt ut labore</div>

<div class="abs ficon" style="left:79px;top:1597px"><svg width="50" height="32" viewBox="0 0 50 32"><path d="M2 16Q25-8 48 16Q25 40 2 16Z" fill="none" stroke="#ff6a00" stroke-width="2.5"/><circle cx="25" cy="16" r="7" fill="none" stroke="#ff6a00" stroke-width="2.5"/><circle cx="25" cy="16" r="2.5" fill="#ff6a00"/></svg></div>
<div class="abs feature-title" style="left:79px;top:1694px">CLEAR EXECUTIVE VISION</div>
<div class="abs feature-text" style="left:79px;top:1725px">dolore magna aliquat enim ad<br>minim veniam quis nostrud.</div>

<div class="abs ficon" style="left:79px;top:1819px"><svg width="50" height="40" viewBox="0 0 50 40"><circle cx="13" cy="27" r="10" fill="none" stroke="#ff6a00" stroke-width="2.5"/><circle cx="37" cy="27" r="10" fill="none" stroke="#ff6a00" stroke-width="2.5"/><path d="M8 18L14 4h6v14M42 18L36 4h-6v14M20 12h10" fill="none" stroke="#ff6a00" stroke-width="2.5"/></svg></div>
<div class="abs feature-title" style="left:79px;top:1928px">EMPLOYEE RETENTION</div>
<div class="abs feature-text" style="left:79px;top:1959px">dolore magna aliquat enim ad<br>minim veniam quis nostrud.</div>

<div class="abs ficon" style="left:828px;top:1597px"><svg width="44" height="44" viewBox="0 0 44 44"><path d="M12 26V10a3 3 0 0 1 6 0v10M18 18V6a3 3 0 0 1 6 0v12M24 18V8a3 3 0 0 1 6 0v12M30 20v-6a3 3 0 0 1 6 0v12c0 8-6 14-13 14s-11-6-11-14" fill="none" stroke="#ff6a00" stroke-width="2.3"/><circle cx="32" cy="34" r="7" fill="#fff" stroke="#ff6a00" stroke-width="2"/><path d="M29 34l2 2 4-4" stroke="#ff6a00" stroke-width="2" fill="none"/></svg></div>
<div class="abs feature-title" style="left:828px;top:1694px">PASSION &amp; IMPACT</div>
<div class="abs feature-text" style="left:828px;top:1725px">dolore magna aliquat enim ad<br>minim veniam quis nostrud.</div>

<div class="abs ficon" style="left:828px;top:1819px"><svg width="44" height="44" viewBox="0 0 44 44"><rect x="4" y="8" width="36" height="32" rx="3" fill="none" stroke="#ff6a00" stroke-width="2.5"/><path d="M4 16h36M13 4v8M31 4v8" stroke="#ff6a00" stroke-width="2.5"/><path d="M22 21l2.5 5 5.5.6-4 3.8 1 5.4-5-2.6-5 2.6 1-5.4-4-3.8 5.5-.6z" fill="none" stroke="#ff6a00" stroke-width="1.8"/></svg></div>
<div class="abs feature-title" style="left:828px;top:1928px">EVENT PLANNER</div>
<div class="abs feature-text" style="left:828px;top:1959px">dolore magna aliquat enim ad<br>minim veniam quis nostrud.</div>

<svg class="abs" style="left:398px;top:1617px" width="400" height="400" viewBox="0 0 400 400">
  <circle cx="200" cy="200" r="193" fill="none" stroke="#fff" stroke-width="2.5"/>
  <circle cx="200" cy="7" r="6" fill="#fff"/><circle cx="200" cy="393" r="6" fill="#fff"/>
  <circle cx="7" cy="200" r="6" fill="#fff"/><circle cx="393" cy="200" r="6" fill="#fff"/>
  <circle cx="200" cy="200" r="172" fill="#fff"/>
</svg>
<div class="abs" role="img" aria-label="Smiling orange mascot character" style="left:442px;top:1661px;width:312px;height:312px;border-radius:50%;background:radial-gradient(circle at 50% 65%,#fff5ec,#ff8a33 95%);border:8px solid var(--orange)"></div>
<div class="abs btn btn-dark" style="left:459px;top:2066px;width:282px;height:54px">VIEW MORE FEATURES</div>

<!-- promise -->
<div class="abs h2" style="left:79px;top:2324px">WHAT WE PROMISE</div>
<div class="abs body" style="left:79px;top:2392px;width:480px">Lorem ipsum dolor sit amet consectetur adipiscingi elit sed do eiusmod tempor incididunt ut labore eto dolore magna aliqua. Quis ipsum suspendisse des ultrices gravida. Risus commodo viverra maecenas accumsan lacus vel facilisis licius decorat.</div>
<div class="abs btn btn-line" style="left:79px;top:2591px;width:214px;height:52px">CONTACT US</div>
<div class="abs art" role="img" aria-label="Illustration of four diverse coworkers joining hands" style="left:593px;top:2321px;width:510px;height:337px;background:linear-gradient(135deg,#eeeeee,#fbd2b2)"></div>

<!-- why choose -->
<div class="abs art" role="img" aria-label="Illustration of a team climbing stairs toward a flag" style="left:74px;top:2790px;width:469px;height:370px;background:linear-gradient(135deg,#f1f1f1,#f9c9a5)"></div>
<div class="abs h2" style="left:635px;top:2824px">WHY CHOOSE US</div>
<div class="abs body" style="left:635px;top:2892px">Lorem ipsum dolor sit amet consectetur adipiscingi<br>elit sed do eiusmod tempor incididunt ut labore</div>
<div class="abs" style="left:635px;top:2975px;font-size:18px;font-weight:700;color:#333;display:flex;align-items:center;gap:14px">ADVANTAGE<span style="width:102px;height:1.5px;background:#333;display:block"></span></div>
<ul class="abs list" style="left:635px;top:3004px">
  <li><span class="tick"><svg width="10" height="8" viewBox="0 0 10 8"><path d="M1 4l3 3 5-6" stroke="#fff" stroke-width="1.8" fill="none"/></svg></span>Lorem ipsum dolor sit amet incididunt ut</li>
  <li><span class="tick"><svg width="10" height="8" viewBox="0 0 10 8"><path d="M1 4l3 3 5-6" stroke="#fff" stroke-width="1.8" fill="none"/></svg></span>Lorem ipsum dolor sit amet viverra sid</li>
  <li><span class="tick"><svg width="10" height="8" viewBox="0 0 10 8"><path d="M1 4l3 3 5-6" stroke="#fff" stroke-width="1.8" fill="none"/></svg></span>Risus commodo viverra maecenas</li>
</ul>

<!-- contact -->
<div class="abs contact"></div>
<div class="abs h2" style="left:0;width:1200px;text-align:center;top:3343px;color:var(--white)">CONTACT US</div>
<div class="abs body" style="left:0;width:1200px;text-align:center;top:3412px;color:var(--white)">Lorem ipsum dolor sit amet consectetur adipiscingi<br>elit sed do eiusmod tempor incididunt ut labore</div>
<div class="abs field" style="left:245px;top:3523px;width:331px;height:51px">Enter Your Name</div>
<div class="abs field" style="left:245px;top:3588px;width:331px;height:51px">Email Address</div>
<div class="abs field" style="left:245px;top:3654px;width:331px;height:51px">Phone No</div>
<div class="abs field" style="left:593px;top:3523px;width:362px;height:182px">Leave your message !</div>
<div class="abs btn btn-fill" style="left:499px;top:3731px;width:202px;height:52px;font-size:14px">SUBMIT NOW</div>

<!-- footer -->
<div class="abs fh" style="left:79px">ABOUT US</div>
<div class="abs flist" style="left:79px;top:3965px">Lorem ipsum dolor sit amet consecter<br>adipiscingi elit sed do eiusmod tempor<br>incididunt ut labore vsiverra idm tote</div>
<div class="abs social" style="left:79px"></div>
<div class="abs social" style="left:136px"></div>
<div class="abs social" style="left:195px"></div>
<div class="abs" style="left:79px;top:4144px;font-size:16px;color:#444">Copyright © 2022 <span style="color:var(--orange)">Velrato.</span></div>

<div class="abs fh" style="left:477px">QUICK LINKS</div>
<div class="abs flist" style="left:477px;top:3965px">Home<br>About Us<br>Our Features<br>Blog<br>Contact</div>

<div class="abs fh" style="left:675px">OTHERS LINK</div>
<div class="abs flist" style="left:675px;top:3965px">Terms &amp; Condition<br>Privacy Policy<br>Cookie<br>Resister Now<br>User Login</div>

<div class="abs fh" style="left:890px">CONTACT INFO</div>
<div class="abs cicon" style="left:890px;top:3974px"><svg width="20" height="20" viewBox="0 0 24 24"><path fill="#fff" d="M6.6 10.8a15 15 0 0 0 6.6 6.6l2.2-2.2c.3-.3.7-.4 1-.2 1.1.4 2.3.6 3.6.6.6 0 1 .4 1 1V20c0 .6-.4 1-1 1A17 17 0 0 1 3 4c0-.6.4-1 1-1h3.5c.6 0 1 .4 1 1 0 1.3.2 2.5.6 3.6.1.3 0 .7-.2 1z"/></svg></div>
<div class="abs flist" style="left:962px;top:3967px;line-height:28px">Phone:<br>555-318-2046</div>
<div class="abs cicon" style="left:890px;top:4041px"><svg width="20" height="18" viewBox="0 0 24 20"><rect x="1" y="3" width="22" height="16" rx="2" fill="#fff"/><path d="M2 5l10 7 10-7" stroke="#ff6a00" stroke-width="2" fill="none"/></svg></div>
<div class="abs flist" style="left:962px;top:4033px;line-height:28px">Email:<br>contact@velrato.com</div>
<div class="abs" style="left:890px;top:4116px;font-size:16.5px;font-weight:500;color:var(--ink);border-bottom:1.5px solid var(--ink);display:flex;align-items:center;gap:8px">Find Us on Map <svg width="16" height="12" viewBox="0 0 16 12"><path d="M1 6h13M9 1l5 5-5 5" stroke="#111" stroke-width="2" fill="none"/></svg></div>

</body>
</html>
```